Responsive OnePage Design for recruitment company

BrightHire is a modern company that sources interim people for its customers. Mostly developers, scrum master, project managers and designers. In this website we want to tell something about us, about how we work, our customers and we want our candidates be able to subscribe. The subscription form should be several fields (name, surname, email address, phone number and the possibility to upload your resume.We want it to fit into a existing wordpress plugin. We also want a listing of our job opportunities. The listing should be designed in a clear readable overview and if you click on the job you should get the details and be able to respond quickly by filling in you name, surname, email address, rate, phone number and upload your resume. We want this to be a standard configurable plugin. It should be easy to fill in the jobs in Wordpress by our administrator. We want a fresh, modern and cool design. It should be a responsive onepage design. If you click on a listed job you should stay on the same page. Our logo is added.

Target Market(s)

recruitment

Industry/Entity Type

Recruitment

Font styles to use
Sans Serif

Colors

Designer to choose colors to be used in the design.

Requirements
Must have
• Onepage design
• listing of job opportunities
• subscription forms
• be responsive

```html
<!DOCTYPE html>
<html lang="en">
<head>
<meta charset="utf-8">
<title>BrightHire — Recruitment Agency</title>
<link href="https://fonts.googleapis.com/css2?family=Poppins:wght@400;500;600;700&family=PT+Sans:wght@400;700&display=swap" rel="stylesheet">
<style>
:root{
  --blue:#1759ad;
  --blue-dark:#124a92;
  --ink:#1f2226;
  --text:#4d5258;
  --muted:#8a8f95;
  --line:#d9dbde;
  --paper:#ffffff;
  --soft:#f2f1f2;
  --navy:#0c1829;
  --footer:#1c1d20;
  --teal:#1e9a98;
}
*{box-sizing:border-box;margin:0;padding:0}
html,body{width:1200px;height:4663px;overflow:hidden}
body{position:relative;background:var(--paper);font-family:"PT Sans",Arial,sans-serif;color:var(--text)}
.abs{position:absolute}
h1,h2,h3,h4,.display{font-family:"Poppins",Arial,sans-serif;color:var(--ink)}
.btn{position:absolute;display:flex;align-items:center;justify-content:center;gap:8px;background:var(--blue);color:#fff;font-family:"Poppins",Arial,sans-serif;font-weight:600;text-transform:uppercase;letter-spacing:.5px}

/* hero */
.hero{position:absolute;left:0;top:0;width:1200px;height:675px;background:linear-gradient(180deg,#cfd0d2 0%,#8e9094 35%,#55585d 70%,#3a3c40 100%)}
.hero-photo{position:absolute;left:0;top:380px;width:1200px;height:295px;background:radial-gradient(ellipse 60% 50% at 50% 40%,rgba(230,230,232,.35),rgba(0,0,0,0))}
.brand{position:absolute;left:40px;top:28px;font-family:"Poppins",Arial,sans-serif;font-weight:600;font-size:30px;letter-spacing:5px;color:#1e5ba8}
.nav{position:absolute;right:40px;top:38px;display:flex;gap:34px;font-family:"Poppins",Arial,sans-serif;font-weight:600;font-size:12.5px;color:#fff;letter-spacing:.3px}
.nav .active{border-bottom:2px solid #fff;padding-bottom:4px}
.hero-title{position:absolute;left:0;width:1200px;top:145px;text-align:center;font-weight:700;font-size:48px;color:#fff;letter-spacing:.5px}
.hero-btn{position:absolute;left:513px;top:240px;width:174px;height:52px;border:3px solid #fff;display:flex;align-items:center;justify-content:center;gap:10px;color:#fff;font-family:"Poppins",Arial,sans-serif;font-weight:600;font-size:14px}

/* about */
.about{position:absolute;left:0;top:675px;width:1200px;height:637px;background:var(--soft)}
.about-frame{position:absolute;left:157px;top:75px;width:454px;height:484px;background:#fff;box-shadow:0 4px 14px rgba(0,0,0,.12)}
.about-art{position:absolute;left:143px;top:62px;width:454px;height:484px;background:radial-gradient(ellipse 30% 40% at 62% 45%,#5fc4c1,var(--teal) 70%)}
.tag{position:absolute;left:672px;top:130px;background:var(--ink);color:#fff;font-family:"Poppins",Arial,sans-serif;font-weight:600;font-size:12px;padding:5px 10px;letter-spacing:1px}
.about h2{position:absolute;left:672px;top:162px;font-size:42px;font-weight:700;color:#1e5ba8;letter-spacing:1px}
.about p{position:absolute;left:672px;top:248px;width:385px;font-size:14.5px;line-height:21px}
.about .btn{left:672px;top:488px;width:132px;height:38px;font-size:13px}

/* how we work */
.how{position:absolute;left:0;top:1312px;width:1200px;height:584px;background:linear-gradient(90deg,var(--navy) 0%,#10213a 45%,#1d3556 75%,#2a4566 100%)}
.how h2{position:absolute;left:143px;top:72px;font-size:36px;font-weight:600;color:#fff}
.how .bar{position:absolute;left:143px;top:128px;width:92px;height:3px;background:#fff}
.how h3{position:absolute;left:143px;top:158px;width:420px;font-size:16px;font-weight:600;color:#fff;line-height:22px;text-transform:uppercase}
.how p{position:absolute;left:143px;top:228px;width:440px;font-size:15.5px;line-height:22px;color:#dfe4ea}
.features{position:absolute;left:143px;top:1753px;width:911px;height:252px;background:var(--blue);display:flex}
.feature{flex:1;padding:30px 34px;color:#fff}
.feature .ico{width:70px;height:70px;margin-bottom:22px}
.feature h4{color:#fff;font-size:17px;font-weight:600;margin-bottom:10px}
.feature p{font-size:13px;line-height:17px;color:#d8e3f3}

/* jobs */
.section-title{position:absolute;left:0;width:1200px;text-align:center;font-size:32px;font-weight:700}
.divider{position:absolute;left:575px;width:50px;height:3px;background:#b9bcc0}
.job{position:absolute;width:449px;height:228px;background:#fff;box-shadow:0 2px 12px rgba(0,0,0,.12)}
.job .ico{position:absolute;left:28px;top:34px;width:62px;height:62px}
.job h4{position:absolute;left:118px;top:30px;font-size:17px;font-weight:600}
.job .posted{position:absolute;left:118px;top:57px;font-size:12px;color:var(--muted)}
.job .meta{position:absolute;left:118px;top:78px;display:flex;gap:12px;font-size:12px;color:var(--muted);align-items:center}
.job .meta span{display:flex;gap:5px;align-items:center}
.job .desc{position:absolute;left:28px;top:122px;width:370px;font-size:13px;line-height:17px}
.job .btn{left:28px;top:177px;width:96px;height:23px;font-size:10.5px}

/* subscription */
.subscribe{position:absolute;left:0;top:3114px;width:1200px;height:631px;background:#eeedee}
.sub-card{position:absolute;left:143px;top:81px;width:911px;height:460px;background:#fff;box-shadow:0 3px 14px rgba(0,0,0,.12)}
.sub-art{position:absolute;left:0;top:0;width:420px;height:460px;background:radial-gradient(ellipse 45% 40% at 50% 55%,#f6b334 0%,#f2a524 40%,#c9ecea 42%,#c3e8e6 100%)}
.sub-card h2{position:absolute;left:450px;top:48px;font-size:30px;font-weight:700}
.field{position:absolute;height:40px;border:1px solid #cfd2d6;font-family:"Poppins",Arial,sans-serif;font-size:11px;color:#7a7f85;padding:0 14px;display:flex;align-items:center;text-transform:uppercase}
.upload{position:absolute;right:6px;top:6px;height:26px;padding:0 12px;background:var(--blue);color:#fff;font-weight:600;display:flex;align-items:center;gap:6px}
.sub-card .btn{left:450px;top:352px;width:100px;height:38px;font-size:13px}

/* customers */
.customers-grid{position:absolute;left:150px;top:3950px;width:900px;display:grid;grid-template-columns:repeat(6,150px);row-gap:50px}
.customer{height:88px;display:flex;align-items:center;justify-content:center;gap:8px;font-family:"Poppins",Arial,sans-serif;font-weight:600;font-size:15px;color:#3a3d41;text-transform:uppercase;text-align:center}
.customer i{display:block;width:14px;height:14px;border-radius:50%;background:#3a3d41;flex:none}

/* footer */
.footer{position:absolute;left:0;top:4236px;width:1200px;height:427px;background:var(--footer);overflow:hidden;color:#c9ccd0}
.footer h5{position:absolute;top:67px;font-family:"Poppins",Arial,sans-serif;font-size:12px;font-weight:600;color:#fff;letter-spacing:.5px}
.f-row{position:absolute;display:flex;gap:14px;font-size:12px;line-height:17px;align-items:flex-start}
.links{position:absolute;left:400px;top:100px;font-size:11.5px;line-height:17px;text-transform:uppercase;list-style:none}
.social{position:absolute;left:612px;display:flex;align-items:center;gap:12px;font-size:12px}
.social i{width:24px;height:24px;border-radius:50%;background:var(--blue);display:block}
.finput{position:absolute;left:833px;width:232px;background:#fff;color:#555;font-size:11px;padding:8px 10px}
.footer .btn{left:833px;top:344px;width:232px;height:36px;font-size:13px}
.wordmark{position:absolute;left:0;top:305px;width:1200px;text-align:center;font-family:"Poppins",Arial,sans-serif;font-weight:600;font-size:170px;letter-spacing:18px;color:rgba(255,255,255,.04);line-height:1}
.copy{position:absolute;left:140px;top:350px;font-size:11px;color:#9a9ea3}
</style>
</head>
<body>

<header class="hero">
  <div class="hero-photo" role="img" aria-label="Photo of a row of white chairs with one blue chair, labelled for developers, scrum masters and project managers"></div>
  <div class="brand">BRIGHTHIRE</div>
  <nav class="nav"><span class="active">HOME</span><span>ABOUT US</span><span>HOW WE WORK</span><span>JOBS</span><span>SUBSCRIBE</span><span>OUR CUSTOMERS</span></nav>
  <h1 class="hero-title">RECRUITMENT AGENCY</h1>
  <div class="hero-btn">
    <svg width="16" height="12" viewBox="0 0 16 12"><rect x="0" y="0" width="16" height="12" fill="#fff"/><path d="M0 0 L8 7 L16 0" fill="none" stroke="#55585d" stroke-width="1.5"/></svg>
    SUBSCRIBE NOW
  </div>
</header>

<section class="about">
  <div class="about-frame"></div>
  <div class="about-art" role="img" aria-label="Illustration of a spotlight singling out one candidate among a group of business people"></div>
  <span class="tag">ABOUT US</span>
  <h2>BRIGHTHIRE</h2>
  <p>Sed ut perspiciatis unde omnis iste natus error sit voluptatem accusantium doloremque laudantium, totam rem aperiam, eaque ipsa quae ab illo inventore veritatis et quasi architecto beatae vitae dicta sunt explicabo. Nemo enim ipsam voluptatem quia voluptas sit aspernatur aut odit aut fugit, sed quia consequuntur magni dolores eos qui ratione voluptatem sequi nesciunt. Neque porro quisquam est, qui dolorem ipsum quia dolor sit amet, consectetur, adipisci velit, sed quia non numquam eius modi tempora incidunt.</p>
  <div class="btn">READ MORE</div>
</section>

<section class="how" role="img" aria-label="Photo of a hand holding a magnifying glass over a network of people icons">
  <h2>HOW WE WORK</h2>
  <div class="bar"></div>
  <h3>Voluptas sit aspernatur aut odit aut fugit sed quia consequuntur</h3>
  <p>Sed ut perspiciatis unde omnis iste natus error sit voluptatem accusantium doloremque laudantium totam rem aperiam eaque ipsa quae ab illo inven tore veritatis et quasi architecto beatae vitae dicta sunt explicabo. Nemo enim ipsam voluptatem quia voluptas sit aspernatur aut odit .</p>
</section>

<div class="features">
  <div class="feature">
    <svg class="ico" viewBox="0 0 70 70"><circle cx="35" cy="35" r="33" fill="#fff"/><circle cx="37" cy="31" r="13" fill="none" stroke="#1759ad" stroke-width="4"/><line x1="28" y1="40" x2="18" y2="51" stroke="#1759ad" stroke-width="6" stroke-linecap="round"/><circle cx="37" cy="28" r="4" fill="#1759ad"/><path d="M30 38 q7-8 14 0" fill="#1759ad"/></svg>
    <h4>Complete Recruitment</h4>
    <p>Sed ut perspiciatis unde omnis iste natus error sit voluptatem accus antium doloremque</p>
  </div>
  <div class="feature">
    <svg class="ico" viewBox="0 0 70 70"><circle cx="35" cy="35" r="33" fill="#fff"/><circle cx="35" cy="22" r="7" fill="#1759ad"/><path d="M22 42 q13-16 26 0z" fill="#1759ad"/><rect x="18" y="44" width="34" height="6" fill="#1759ad"/><rect x="24" y="52" width="22" height="4" fill="#1759ad"/></svg>
    <h4>Recruitment Process</h4>
    <p>Sed ut perspiciatis unde omnis iste natus error sit voluptatem accus antium doloremque</p>
  </div>
  <div class="feature">
    <svg class="ico" viewBox="0 0 70 70"><circle cx="35" cy="35" r="33" fill="#fff"/><circle cx="35" cy="30" r="14" fill="none" stroke="#1759ad" stroke-width="4"/><path d="M29 30 l4 4 l8-8" fill="none" stroke="#1759ad" stroke-width="3"/><path d="M26 42 l-5 14 l7-3 l4 6 l3-12z M44 42 l5 14 l-7-3 l-4 6 l-3-12z" fill="#1759ad"/></svg>
    <h4>Premium Jos posting</h4>
    <p>Sed ut perspiciatis unde omnis iste natus error sit voluptatem accus antium doloremque</p>
  </div>
</div>

<h2 class="section-title" style="top:2072px">LATEST JOBS</h2>
<div class="divider" style="top:2142px"></div>

<article class="job" style="left:143px;top:2216px">
  <svg class="ico" viewBox="0 0 62 62" fill="none" stroke="#1759ad" stroke-width="2.5"><rect x="6" y="24" width="50" height="30"/><circle cx="20" cy="12" r="6"/><circle cx="42" cy="12" r="6"/><polyline points="14,46 24,36 32,42 46,30"/></svg>
  <h4>Business Analyst</h4><div class="posted">Posted on March 01, 2019</div>
  <div class="meta"><span>&#9679; Los Angeles</span>|<span>&#9711; Full/Part-time</span></div>
  <p class="desc">Sed ut perspiciatis unde omnis iste natus error sit voluptatem accus antium doloremque</p>
  <div class="btn">APPLY NOW</div>
</article>
<article class="job" style="left:622px;top:2216px">
  <svg class="ico" viewBox="0 0 62 62" fill="none" stroke="#1759ad" stroke-width="2.5"><rect x="8" y="8" width="34" height="26"/><circle cx="42" cy="40" r="8"/><path d="M28 60 q14-18 28 0"/><line x1="14" y1="16" x2="34" y2="16"/><line x1="14" y1="24" x2="28" y2="24"/></svg>
  <h4>Project Manager</h4><div class="posted">Posted on March 01, 2019</div>
  <div class="meta"><span>&#9679; Los Angeles</span>|<span>&#9711; Full/Part-time</span></div>
  <p class="desc">Sed ut perspiciatis unde omnis iste natus error sit voluptatem accus antium doloremque</p>
  <div class="btn">APPLY NOW</div>
</article>
<article class="job" style="left:143px;top:2468px">
  <svg class="ico" viewBox="0 0 62 62" fill="none" stroke="#1759ad" stroke-width="2.5"><rect x="6" y="8" width="50" height="36"/><polyline points="24,20 16,26 24,32"/><polyline points="38,20 46,26 38,32"/><line x1="20" y1="54" x2="42" y2="54"/><line x1="31" y1="44" x2="31" y2="54"/></svg>
  <h4>Software Engineer</h4><div class="posted">Posted on March 01, 2019</div>
  <div class="meta"><span>&#9679; Los Angeles</span>|<span>&#9711; Full/Part-time</span></div>
  <p class="desc">Sed ut perspiciatis unde omnis iste natus error sit voluptatem accus antium doloremque</p>
  <div class="btn">APPLY NOW</div>
</article>
<article class="job" style="left:622px;top:2468px">
  <svg class="ico" viewBox="0 0 62 62" fill="none" stroke="#1759ad" stroke-width="2.5"><rect x="4" y="10" width="54" height="34"/><rect x="22" y="24" width="18" height="14"/><path d="M25 24 v-5 a6 6 0 0 1 12 0 v5"/><line x1="20" y1="54" x2="42" y2="54"/></svg>
  <h4>IT Security</h4><div class="posted">Posted on March 01, 2019</div>
  <div class="meta"><span>&#9679; Los Angeles</span>|<span>&#9711; Full/Part-time</span></div>
  <p class="desc">Sed ut perspiciatis unde omnis iste natus error sit voluptatem accus antium doloremque</p>
  <div class="btn">APPLY NOW</div>
</article>
<article class="job" style="left:143px;top:2713px">
  <svg class="ico" viewBox="0 0 62 62" fill="none" stroke="#1759ad" stroke-width="2.5"><rect x="4" y="6" width="20" height="14"/><rect x="38" y="6" width="20" height="14"/><rect x="4" y="42" width="20" height="14"/><rect x="38" y="42" width="20" height="14"/><rect x="24" y="24" width="14" height="14"/><line x1="14" y1="20" x2="24" y2="28"/><line x1="48" y1="20" x2="38" y2="28"/><line x1="14" y1="42" x2="24" y2="34"/><line x1="48" y1="42" x2="38" y2="34"/></svg>
  <h4>Data Scientist</h4><div class="posted">Posted on March 01, 2019</div>
  <div class="meta"><span>&#9679; Los Angeles</span>|<span>&#9711; Full/Part-time</span></div>
  <p class="desc">Sed ut perspiciatis unde omnis iste natus error sit voluptatem accus antium doloremque</p>
  <div class="btn">APPLY NOW</div>
</article>
<article class="job" style="left:622px;top:2713px">
  <svg class="ico" viewBox="0 0 62 62" fill="none" stroke="#1759ad" stroke-width="2.5"><rect x="4" y="6" width="54" height="50"/><line x1="4" y1="16" x2="58" y2="16"/><polyline points="24,26 16,34 24,42"/><polyline points="38,26 46,34 38,42"/><line x1="34" y1="24" x2="28" y2="44"/></svg>
  <h4>Program Manager</h4><div class="posted">Posted on March 01, 2019</div>
  <div class="meta"><span>&#9679; Los Angeles</span>|<span>&#9711; Full/Part-time</span></div>
  <p class="desc">Sed ut perspiciatis unde omnis iste natus error sit voluptatem accus antium doloremque</p>
  <div class="btn">APPLY NOW</div>
</article>

<div class="btn" style="left:520px;top:3005px;width:160px;height:44px;font-size:13.5px">VIEW ALL JOBS</div>

<section class="subscribe">
  <div class="sub-card">
    <div class="sub-art" role="img" aria-label="Illustration of an open orange envelope with a letter, a paper plane and clouds"></div>
    <h2>SUBSCRIPTION</h2>
    <div class="field" style="left:450px;top:150px;width:205px">Name</div>
    <div class="field" style="left:671px;top:150px;width:205px">Surname</div>
    <div class="field" style="left:450px;top:210px;width:205px">Email Address</div>
    <div class="field" style="left:671px;top:210px;width:205px">Phone Number</div>
    <div class="field" style="left:450px;top:272px;width:426px">Upload Resume
      <span class="upload"><svg width="10" height="11" viewBox="0 0 10 11"><path d="M5 0 L9 4 H6 V8 H4 V4 H1z M0 9 H10 V11 H0z" fill="#fff"/></svg>UPLOAD</span>
    </div>
    <div class="btn">SEND</div>
  </div>
</section>

<h2 class="section-title" style="top:3808px">OUR CUSTOMERS</h2>
<div class="divider" style="top:3878px"></div>
<div class="customers-grid">
  <div class="customer">Fretline</div>
  <div class="customer"><i></i>Northpeak</div>
  <div class="customer">Velora</div>
  <div class="customer"><i></i>Stagfield</div>
  <div class="customer">Ironleaf</div>
  <div class="customer">Tallis</div>
  <div class="customer">Kestrel Co</div>
  <div class="customer"><i></i>Ashgrove</div>
  <div class="customer">Loomwell</div>
  <div class="customer">Bramble Table</div>
  <div class="customer"><i></i>Cobalt &amp; Oak</div>
  <div class="customer">Velora</div>
</div>

<footer class="footer">
  <div class="wordmark">BRIGHTHIRE</div>
  <h5 style="left:140px">GET IN TOUCH</h5>
  <h5 style="left:400px">QUICK LINKS</h5>
  <h5 style="left:612px">CONNECT WITH US</h5>
  <h5 style="left:833px">CONTACT US</h5>

  <div class="f-row" style="left:140px;top:112px"><svg width="12" height="12" viewBox="0 0 12 12"><path d="M2 0 L5 3 L3.5 5 Q5 8 7 8.5 L9 7 L12 10 L10 12 Q2 11 0 2z" fill="#fff"/></svg><span>555 010 2030</span></div>
  <div class="f-row" style="left:140px;top:150px"><svg width="13" height="10" viewBox="0 0 13 10"><rect width="13" height="10" fill="#fff"/><path d="M0 0 L6.5 6 L13 0" fill="none" stroke="#1c1d20" stroke-width="1.2"/></svg><span>hello@brighthire.example</span></div>
  <div class="f-row" style="left:140px;top:188px"><svg width="11" height="14" viewBox="0 0 11 14"><path d="M5.5 0 A5.5 5.5 0 0 1 11 5.5 Q11 9 5.5 14 Q0 9 0 5.5 A5.5 5.5 0 0 1 5.5 0z" fill="#fff"/><circle cx="5.5" cy="5.5" r="2" fill="#1c1d20"/></svg><span>12 Harbour Works<br>Mill Road, Camford<br>CF4 0XQ</span></div>

  <ul class="links"><li>Home</li><li>About us</li><li>How we work</li><li>Our customers</li><li>Jobs</li><li>Subscribe</li></ul>

  <div class="social" style="top:106px"><i></i>Friendlink</div>
  <div class="social" style="top:146px"><i></i>Chirper</div>
  <div class="social" style="top:186px"><i></i>WorkNet</div>

  <div class="finput" style="top:94px;height:30px">Your Name</div>
  <div class="finput" style="top:132px;height:30px">Your E-mail</div>
  <div class="finput" style="top:170px;height:30px">Subject</div>
  <div class="finput" style="top:210px;height:110px">Message</div>
  <div class="btn">SUBMIT</div>

  <div class="copy">Copyrights © 2019 All Rights Reserved</div>
</footer>

</body>
</html>
```